Web Design for an Innovative Life Science Marketplace

IMPORTANT:
The software is called CS-Cart. It has capabilities and limitations with design features in the software. There is a certain framework that needs to be followed. It is PHP and Linux. It may require add-ons for your design, so please be specific with what is required. It’s preferred the designer has CS-Cart knowledge/experience.

Key Requirements
1. I’d like the design to include an implemented/recommended CS-Cart theme that is consistent with our branding (see the marketing collateral and logo).
2. I then need the additional design changes to that theme to create the below web pages.
3. All designs should be consistent with our branding. All pictures should either be computer generated (clip art-like) or pictures of happy patients. What is a happy patient? Close up photo of someone healthy, happy, and experiencing/enjoying life. Not someone in a hospital or getting care. Please see examples already on the site.

Please see the attached Web Design details in the word document. That document is important to complete the design.

```html
<!DOCTYPE html>
<html lang="en">
<head>
<meta charset="utf-8">
<title>Loopsource-LS — Join the Circular Supply Chain</title>
<link rel="stylesheet" href="https://fonts.googleapis.com/css2?family=Roboto+Condensed:wght@600;700&family=Montserrat:wght@400;500&family=Arimo:wght@400&family=Open+Sans:wght@400&display=swap">
<style>
:root{
  --teal:#16877a;
  --teal-dark:#0f6f64;
  --green:#8cc63f;
  --green-bright:#9acd3c;
  --ink:#111;
  --grey-text:#8a8a8a;
  --footer:#2d2d2d;
  --footer-text:#9a9a9a;
  --white:#fff;
  --display:"Roboto Condensed","Arial Narrow",sans-serif;
}
*{box-sizing:border-box;margin:0;padding:0}
html,body{width:1200px;height:2403px;overflow:hidden}
body{position:relative;background:var(--white);font-family:"Arimo",Arial,sans-serif;color:var(--ink)}
.abs{position:absolute}

/* header */
.site-header{left:0;top:0;width:1200px;height:104px;background:var(--white)}
.brand{left:78px;top:28px;display:flex;align-items:center;gap:10px}
.brand-dot{width:40px;height:40px;border-radius:50%;background:var(--green)}
.brand-name{font-family:var(--display);font-weight:700;font-size:26px;color:var(--teal);letter-spacing:.5px}
.main-nav{right:78px;top:46px;display:flex;gap:40px;font-family:"Montserrat",sans-serif;font-size:12.5px;color:var(--green)}
.main-nav .active{color:var(--teal)}

/* hero */
.hero{left:0;top:104px;width:1200px;height:620px}
.hero-photo{left:0;top:0;width:1200px;height:620px;background:linear-gradient(120deg,#6b5a4e 0%,#4a3b35 40%,#5c4a40 70%,#3e3430 100%)}
.hero-shade{left:0;top:0;width:1200px;height:620px;background:rgba(0,0,0,.42)}
.hero-title{left:0;top:166px;width:1200px;text-align:center;font-family:var(--display);font-weight:700;font-size:58px;line-height:70px;color:var(--white);letter-spacing:.5px}
.hero-sub{left:0;top:254px;width:1200px;text-align:center;font-family:"Montserrat",sans-serif;font-size:19px;line-height:24px;color:var(--white)}
.hero-cta{left:465px;top:324px;width:270px;height:51px;background:var(--white);border-radius:3px;display:flex;align-items:center;justify-content:center;font-family:"Montserrat",sans-serif;font-weight:500;font-size:19px;color:#222}
.hero-curve{left:0;top:560px;width:1200px;height:180px}

/* audience cards */
.card{top:680px;width:335px;height:220px;border-left:2px solid #f0f0f0;border-right:2px solid #f0f0f0;text-align:center}
.card-title{position:absolute;top:100px;width:100%;font-family:var(--display);font-weight:700;font-size:23px;color:#1a1a1a}
.card-text{position:absolute;top:143px;left:20px;right:20px;font-family:"Montserrat",sans-serif;font-size:13px;line-height:21px;color:var(--grey-text)}
.card-icon{top:593px;width:146px;height:146px;border-radius:50%;background:var(--white);border:5px solid var(--green);display:flex;align-items:center;justify-content:center}
.card-icon .art{width:112px;height:112px;border-radius:50%;background:#eceded}

/* products */
.products{left:0;top:969px;width:1200px;height:417px;background:linear-gradient(90deg,var(--teal) 0%,#4fa85e 55%,var(--green-bright) 100%)}
.products-title{left:0;top:62px;width:1200px;text-align:center;font-family:var(--display);font-weight:700;font-size:36px;color:var(--white)}
.product-frame{top:126px;width:216px;height:168px;overflow:hidden}
.product-art{position:absolute;left:4px;top:4px;width:208px;height:208px;border-radius:50%;border:5px solid var(--white);box-shadow:0 0 0 3px var(--teal-dark)}
.product-label{top:295px;width:231px;height:63px;border:2px solid var(--white);display:flex;align-items:center;justify-content:center;font-family:var(--display);font-weight:600;font-size:20px;white-space:nowrap;color:var(--white)}
.product-label.active{background:var(--white);color:var(--teal)}

/* documents */
.doc{top:1386px;width:600px;height:363px;text-align:center}
.doc-left{left:0;background:linear-gradient(90deg,#e9e6e2,#f3f3f3)}
.doc-right{left:600px;background:linear-gradient(90deg,#fbfbfb,#f2f2f2)}
.doc-title{position:absolute;top:72px;width:100%;font-family:var(--display);font-weight:700;font-size:29px;color:var(--ink)}
.doc-text{position:absolute;top:135px;left:40px;right:40px;font-family:"Arimo",sans-serif;font-size:16px;line-height:26px;color:#8c8c8c}
.doc-btn{position:absolute;top:242px;height:51px;width:280px;background:var(--teal);color:var(--white);border-radius:2px;display:flex;align-items:center;justify-content:center;font-family:"Montserrat",sans-serif;font-weight:500;font-size:19px}

/* promise */
.promise-title{left:0;top:1808px;width:1200px;text-align:center;font-family:var(--display);font-weight:700;font-size:38px;color:var(--ink)}
.promise-text{left:270px;top:1876px;width:660px;text-align:center;font-family:"Arimo",sans-serif;font-size:16px;line-height:26px;color:#8c8c8c}

/* footer */
.footer-shape{left:0;top:1970px;width:1200px;height:390px}
.footer-badge{left:563px;top:1950px;width:74px;height:74px;border-radius:50%;background:var(--white);border:3px solid var(--teal);box-shadow:0 0 0 4px var(--white)}
.footer-col{top:2085px;width:250px;font-family:"Open Sans",sans-serif}
.footer-col h3{font-weight:400;font-size:21px;color:var(--white);letter-spacing:.5px;margin-bottom:18px}
.footer-col ul{list-style:none}
.footer-col li{font-size:15px;color:var(--footer-text);height:31px;display:flex;align-items:center;gap:8px}
.footer-col li.current{color:var(--white)}
.chev{font-size:14px;letter-spacing:-3px;color:inherit}
.footer-divider{top:2085px;width:1px;height:240px;background:#3d3d3d}
.contact-row{display:flex;gap:14px;align-items:flex-start;font-size:14px;line-height:22px;color:var(--white);margin-bottom:20px}
.contact-row svg{flex:none;margin-top:3px}
.bottom-bar{left:0;top:2352px;width:1200px;height:51px;background:var(--green);display:flex;align-items:center;justify-content:center;font-family:"Arimo",sans-serif;font-size:13px;color:#3a5a14}
.bottom-bar strong{font-family:var(--display);font-weight:700;font-size:17px;color:#1a1a1a;margin-right:6px}
</style>
</head>
<body>

<header class="site-header abs">
  <div class="brand abs"><span class="brand-dot"></span><span class="brand-name">LOOPSOURCE-LS</span></div>
  <nav class="main-nav abs">
    <span class="active">Home</span><span>About</span><span>Why Loopsource-ls</span><span>Partner</span><span>White Paper</span><span>Quality Policy</span><span>Contact Us</span>
  </nav>
</header>

<section class="hero abs">
  <div class="hero-photo abs" role="img" aria-label="Close-up photo of a group of happy young friends smiling together outdoors"></div>
  <div class="hero-shade abs"></div>
  <h1 class="hero-title abs">JOIN THE CIRCULAR SUPPLY CHAIN</h1>
  <p class="hero-sub abs">A virtual multi-vendor marketplace and for the life sciences community to<br>connect and transact before and after-market materials and equipment</p>
  <a class="hero-cta abs">PRE-REGISTER TODAY</a>
</section>

<svg class="hero-curve abs" viewBox="0 0 1200 180" aria-hidden="true">
  <path d="M0 50 Q600 150 1200 50 L1200 180 L0 180 Z" fill="#fff"/>
  <path d="M120 72 Q600 150 1080 72" fill="none" stroke="#8cc63f" stroke-width="4"/>
  <path d="M540 108 Q600 112 660 108" fill="none" stroke="#16877a" stroke-width="4"/>
</svg>

<div class="card abs" style="left:77px">
  <div class="card-title">MANUFACTURES</div>
  <div class="card-text">Create an Account in Minutes to Sell/Buy Excess or Obsolete Materials and Equipment</div>
</div>
<div class="card abs" style="left:433px">
  <div class="card-title">RESEARCHERS</div>
  <div class="card-text">Sell/Buy Low-Cost Materials and Receive Donations</div>
</div>
<div class="card abs" style="left:788px">
  <div class="card-title">ORIGINAL SUPPLIERS</div>
  <div class="card-text">Market Your Products Across a Broad Life Sciences Network</div>
</div>
<div class="card-icon abs" style="left:171px"><div class="art" role="img" aria-label="Icon of a worker beside a machine"></div></div>
<div class="card-icon abs" style="left:527px;top:630px"><div class="art" role="img" aria-label="Icon of researchers around a magnifying glass and chart"></div></div>
<div class="card-icon abs" style="left:882px"><div class="art" role="img" aria-label="Icon of a supplier connected to a network of people"></div></div>

<section class="products abs">
  <h2 class="products-title abs">PRODUCTS</h2>
  <div class="product-frame abs" style="left:95px"><div class="product-art" style="background:radial-gradient(circle,#c9a67a,#8d8f92)" role="img" aria-label="Photo of assorted raw materials"></div></div>
  <div class="product-frame abs" style="left:360px"><div class="product-art" style="background:radial-gradient(circle,#f2f2f2,#2b2b2b)" role="img" aria-label="Photo of an equipment bag with supplies"></div></div>
  <div class="product-frame abs" style="left:624px"><div class="product-art" style="background:radial-gradient(circle,#ffffff,#37b6c4)" role="img" aria-label="Photo of pill organisers and parts"></div></div>
  <div class="product-frame abs" style="left:888px"><div class="product-art" style="background:radial-gradient(circle,#d9d9d9,#4a4f5a)" role="img" aria-label="Photo of a team meeting around a table"></div></div>
  <div class="product-label active abs" style="left:88px">Raw Materials</div>
  <div class="product-label abs" style="left:353px">Equipment</div>
  <div class="product-label abs" style="left:617px">Parts</div>
  <div class="product-label abs" style="left:881px">Collaborative Relationships</div>
</section>

<section class="doc doc-left abs" role="img" aria-label="Soft background photo of sticky notes on a wall">
  <h2 class="doc-title">OUR WHITE PAPER</h2>
  <p class="doc-text">A virtual multi-vendor marketplace and for the life sciences community to connect and transact before and after-market materials and equipment</p>
  <a class="doc-btn" style="left:162px">READ OUR WHITE PAPER</a>
</section>
<section class="doc doc-right abs" role="img" aria-label="Faded background photo of a brochure cover with a smiling person">
  <h2 class="doc-title">OUR BROCHURE</h2>
  <p class="doc-text">A virtual multi-vendor marketplace and for the life sciences community to connect and transact before and after-market materials and equipment</p>
  <a class="doc-btn" style="left:161px">READ OUR BROCHURE</a>
</section>

<h2 class="promise-title abs">OUR PROMISE</h2>
<p class="promise-text abs">“A greener, more cost-efficient, and quality-driven supply chain through a collaborative life sciences marketplace”</p>

<svg class="footer-shape abs" viewBox="0 0 1200 390" aria-hidden="true">
  <path d="M0 90 Q600 -40 1200 90 L1200 390 L0 390 Z" fill="#2d2d2d"/>
  <path d="M0 90 Q600 -40 1200 90" fill="none" stroke="#8cc63f" stroke-width="5"/>
  <path d="M700 22 Q1000 40 1200 90" fill="none" stroke="#16877a" stroke-width="5"/>
</svg>
<div class="footer-badge abs"></div>

<div class="footer-col abs" style="left:80px">
  <h3>SITE MAP</h3>
  <ul><li><span class="chev">››</span>My Account</li><li><span class="chev">››</span>Signin</li></ul>
</div>
<div class="footer-divider abs" style="left:307px"></div>
<div class="footer-col abs" style="left:343px">
  <h3>CONTACT US</h3>
  <ul>
    <li class="current"><span class="chev">››</span>Home</li>
    <li><span class="chev">››</span>About Us</li>
    <li><span class="chev">››</span>How it Works</li>
    <li><span class="chev">››</span>Our Partner</li>
    <li><span class="chev">››</span>White Paper</li>
  </ul>
</div>
<div class="footer-divider abs" style="left:570px"></div>
<div class="footer-col abs" style="left:606px">
  <h3>FOLLOW US ON</h3>
  <ul><li><span class="chev">››</span>Quality Policy</li><li><span class="chev">››</span>Privacy Policy</li></ul>
</div>
<div class="footer-divider abs" style="left:838px"></div>
<div class="footer-col abs" style="left:870px;width:290px">
  <h3>TESTIMONIAL</h3>
  <div class="contact-row">
    <svg width="16" height="20" viewBox="0 0 16 20"><path d="M8 1a6 6 0 0 0-6 6c0 4.5 6 12 6 12s6-7.5 6-12a6 6 0 0 0-6-6z" fill="none" stroke="#fff" stroke-width="1.4"/><circle cx="8" cy="7" r="2" fill="none" stroke="#fff" stroke-width="1.4"/></svg>
    <span>240 Harbor Row 18<br>Millbrook, PA 15990</span>
  </div>
  <div class="contact-row">
    <svg width="18" height="18" viewBox="0 0 18 18"><path d="M4 1.5l3 3-2 2c1 2.5 3 4.5 5.5 5.5l2-2 3 3-2 2.5C8 15 3 10 1.5 3.5z" fill="none" stroke="#fff" stroke-width="1.4"/></svg>
    <span>+1 800-555-0142</span>
  </div>
  <div class="contact-row">
    <svg width="18" height="14" viewBox="0 0 18 14"><rect x="1" y="1" width="16" height="12" fill="none" stroke="#fff" stroke-width="1.4"/><path d="M1 1l8 7 8-7" fill="none" stroke="#fff" stroke-width="1.4"/></svg>
    <span>info@loopsourcels.com</span>
  </div>
</div>

<footer class="bottom-bar abs">©&nbsp;<strong>LOOPSOURCE-LS - 2018.</strong> Powered by Stallhub – Shopping Cart Software</footer>

</body>
</html>
```